Tolvik Commercial Cleaning is lookong for a new business card design.

A fresh new design that's professional and stylish. We need a serious upgrade to our business cards. I have included pictures of our existing ones. Our clients include professional individuals and business owners. We woupdblike something professional and upbeat. Please have fun and see what you come uo with.

Target Market(s)

Property managers, business owners, facility managers and other similar professionals

Industry/Entity Type

Janitorial

Contact Information for Business Card

Name, cell, office number, email, web address

Font styles to use
Sans Serif

Colors

Designer to choose colors to be used in the design.

Requirements
Must have
• please use the green color in our logo
Nice to have
• Bar code
Should not have
• Address

```html
<!DOCTYPE html>
<html lang="en">
<head>
<meta charset="utf-8">
<title>Tolvik Commercial Cleaning — Business Card</title>
<link rel="stylesheet" href="https://fonts.googleapis.com/css2?family=Open+Sans:wght@400;700&display=swap">
<style>
  :root {
    --backdrop: #232323;
    --card: #fdfdf2;
    --brand-green: #3bb75a;
    --brand-blue: #3a6db0;
    --ink: #1c1c1c;
    --rule: #2a2a2a;
  }
  * { box-sizing: border-box; margin: 0; padding: 0; }
  html, body { width: 1200px; height: 780px; overflow: hidden; }
  body {
    background: var(--backdrop);
    font-family: "Open Sans", sans-serif;
    display: flex;
    align-items: center;
    justify-content: center;
    gap: 44px;
  }
  .card {
    width: 520px;
    height: 297px;
    background: var(--card);
    position: relative;
    box-shadow: 0 10px 24px rgba(0,0,0,0.55);
  }
  .card--front {
    display: flex;
    align-items: center;
    justify-content: center;
  }
  .brand {
    display: flex;
    align-items: center;
    gap: 12px;
  }
  .brand__dot {
    width: 22px; height: 22px;
    border-radius: 50%;
    background: var(--brand-green);
    flex: none;
  }
  .brand__name {
    color: var(--brand-green);
    font-weight: 700;
    line-height: 1.05;
  }
  .card--front .brand__name { font-size: 34px; }
  .card--back .brand__name { font-size: 21px; }
  .card--back .brand__dot { width: 16px; height: 16px; }

  .card--back { display: flex; }
  .card--back .brand-side {
    width: 52%;
    display: flex;
    align-items: center;
    justify-content: center;
    padding-left: 18px;
  }
  .divider {
    position: absolute;
    left: 52%;
    top: 74px;
    width: 1px;
    height: 150px;
    background: var(--rule);
  }
  .contact-side {
    flex: 1;
    padding: 84px 0 0 34px;
  }
  .person {
    font-size: 25px;
    font-weight: 700;
    letter-spacing: -0.2px;
    margin-bottom: 16px;
    white-space: nowrap;
  }
  .person__first { color: var(--brand-green); }
  .person__last { color: var(--brand-blue); }
  .contact-list { list-style: none; }
  .contact-list li {
    display: flex;
    align-items: center;
    gap: 9px;
    font-size: 13.5px;
    color: var(--ink);
    line-height: 1.6;
  }
  .contact-list svg { width: 13px; height: 13px; flex: none; fill: var(--brand-green); }
</style>
</head>
<body>
  <section class="card card--front" aria-label="Card front">
    <div class="brand">
      <span class="brand__dot"></span>
      <span class="brand__name">Tolvik Commercial<br>Cleaning</span>
    </div>
  </section>

  <section class="card card--back" aria-label="Card back">
    <div class="brand-side">
      <div class="brand">
        <span class="brand__dot"></span>
        <span class="brand__name">Tolvik Commercial<br>Cleaning</span>
      </div>
    </div>
    <span class="divider"></span>
    <div class="contact-side">
      <p class="person"><span class="person__first">Mara</span> <span class="person__last">Lindqvist</span></p>
      <ul class="contact-list">
        <li>
          <svg viewBox="0 0 24 24" aria-hidden="true"><path d="M6.6 10.8a15.1 15.1 0 0 0 6.6 6.6l2.2-2.2a1 1 0 0 1 1-.25 11.4 11.4 0 0 0 3.6.57 1 1 0 0 1 1 1V20a1 1 0 0 1-1 1A17 17 0 0 1 3 4a1 1 0 0 1 1-1h3.5a1 1 0 0 1 1 1c0 1.25.2 2.45.57 3.57a1 1 0 0 1-.25 1z"/></svg>
          (555) 014-2280
        </li>
        <li>
          <svg viewBox="0 0 24 24" aria-hidden="true"><path d="M2 5h20v14H2z M4 7v.5l8 5 8-5V7l-8 5z" fill-rule="evenodd"/></svg>
          mara@tolvikcleaning.com
        </li>
        <li>
          <svg viewBox="0 0 24 24" aria-hidden="true"><path d="M12 2a10 10 0 1 0 0 20 10 10 0 0 0 0-20zm-1 17.9A8 8 0 0 1 4.1 11H7c.1 3 .9 6 2.3 8.4zM4.1 9A8 8 0 0 1 9.3 4.6 17 17 0 0 0 7 9zm4.9 2h6c-.1 3-1 5.8-3 8.2-2-2.4-2.9-5.2-3-8.2zm0-2c.2-2.8 1.1-5.3 3-7.2 1.9 1.9 2.8 4.4 3 7.2zm5.7 10.4A18 18 0 0 0 17 11h2.9a8 8 0 0 1-5.2 8.4zM17 9a17 17 0 0 0-2.3-4.4A8 8 0 0 1 19.9 9z"/></svg>
          www.tolvikcleaning.com
        </li>
      </ul>
    </div>
  </section>
</body>
</html>
```